VFX Company Business Card Design Project

The Kestrel Works is a decentralized Visual Effects Studio servicing the television and feature film industries.
Project Brief:
Take our logo that was previously designed on Pencil Harbor and make a double sided business card.
Requirements:
- Card MUST be double sided.
- Front of card MUST have the yellow part of our logo against the dark grey background.
- Back of card is completely up to the designer.
- Back of card must include the complete company logo.
Please follow these File Preparation guidelines:
http://printnook.ca/infopage?file=filetype_en&s=PrintNook_new&lang=en
Business

```html
<!DOCTYPE html>
<html lang="en">
<head>
<meta charset="utf-8">
<title>The Kestrel Works – Business Card</title>
<link rel="stylesheet" href="https://fonts.googleapis.com/css2?family=Jost:ital,wght@0,400;0,500;1,600&family=Source+Sans+3:wght@400&display=swap">
<style>
  :root {
    --backdrop: #c8956b;
    --card: #2b2b2b;
    --label: #1f1a16;
    --brand-yellow: #f7c22c;
    --brand-grey: #6e7476;
    --swoosh-grey: #5f6466;
    --swoosh-light: #e9ebe4;
    --ink-light: #ffffff;
  }
  * { box-sizing: border-box; margin: 0; padding: 0; }
  html, body { width: 1200px; height: 788px; overflow: hidden; }
  body {
    position: relative;
    background: var(--backdrop);
    font-family: "Jost", sans-serif;
    color: var(--ink-light);
  }
  .side-label {
    position: absolute;
    width: 200px;
    text-align: center;
    font-family: "Source Sans 3", sans-serif;
    font-size: 22px;
    color: var(--label);
  }
  .card {
    position: absolute;
    width: 524px;
    height: 300px;
    background: var(--card);
    border-radius: 22px;
    overflow: hidden;
  }
  .card-back { left: 338px; top: 78px; }
  .card-front-one { left: 55px; top: 446px; }
  .card-front-two { left: 623px; top: 446px; }
  .swoosh { position: absolute; inset: 0; width: 524px; height: 300px; }

  .brand-name {
    position: absolute;
    left: 0; right: 0;
    text-align: center;
    font-weight: 500;
    white-space: nowrap;
  }
  .card-back .brand-name { top: 52px; font-size: 40px; color: var(--brand-grey); }

  .holder {
    position: absolute; top: 166px; left: 0; right: 0;
    text-align: center; font-size: 19px;
  }
  .holder .designation { font-size: 14px; }
  .contact-line {
    position: absolute; left: 0; right: 0;
    text-align: center; font-size: 13.5px;
  }
  .contact-line b { font-style: italic; font-weight: 600; }
  .line-phone { top: 201px; }
  .line-web { top: 226px; }
  .line-address { top: 251px; }

  .card-front-one .brand-name { top: 112px; font-size: 50px; color: var(--brand-yellow); }

  .lockup {
    position: absolute; left: 0; right: 0; top: 122px;
    display: flex; justify-content: center; align-items: center; gap: 18px;
  }
  .lockup .dot {
    width: 46px; height: 46px; border-radius: 50%;
    background: var(--brand-yellow);
  }
  .lockup .name { font-size: 36px; font-weight: 500; color: var(--brand-grey); white-space: nowrap; }

  .web-address {
    position: absolute; left: 0; right: 0; top: 256px;
    text-align: center; font-size: 20px; letter-spacing: 3.4px;
  }
</style>
</head>
<body>
  <div class="side-label" style="left:500px; top:32px;">Back</div>
  <section class="card card-back">
    <svg class="swoosh" viewBox="0 0 524 300" aria-hidden="true">
      <path d="M440 0 Q505 8 524 40 L524 0 Z" fill="var(--swoosh-grey)"/>
      <path d="M445 0 Q500 10 524 33" fill="none" stroke="var(--swoosh-light)" stroke-width="2"/>
      <path d="M0 262 Q30 292 100 300 L0 300 Z" fill="var(--swoosh-grey)"/>
      <path d="M0 268 Q30 292 92 300" fill="none" stroke="var(--swoosh-light)" stroke-width="2"/>
    </svg>
    <div class="brand-name">The Kestrel Works</div>
    <div class="holder">Your Name, <span class="designation">Designation</span></div>
    <div class="contact-line line-phone"><b>phone</b> 123-456-7890 &nbsp;|&nbsp; <b>cell</b> 123-456-7890</div>
    <div class="contact-line line-web"><b>email</b> info@kestrelworks.com &nbsp;|&nbsp; <b>web</b> www.kestrelworks.com</div>
    <div class="contact-line line-address">0000#, Area Name, Street Name, State Name, Country code</div>
  </section>

  <div class="side-label" style="left:227px; top:403px;">Front - 1</div>
  <section class="card card-front-one">
    <div class="brand-name">The Kestrel Works</div>
    <div class="web-address">www.kestrelworks.com</div>
  </section>

  <div class="side-label" style="left:800px; top:403px;">Front - 2</div>
  <section class="card card-front-two">
    <div class="lockup">
      <span class="dot"></span>
      <span class="name">The Kestrel Works</span>
    </div>
    <div class="web-address">www.kestrelworks.com</div>
  </section>
</body>
</html>
```